UL Aesthetic improvement on full website

brightneighbourhq.com
We need someone to improve the current website brightneighbourhq.com
Some designed to fail to follow isntruction and deliver. please find attached summary latest design requirement, please follow and read each of the requirements carefully and submit max two versions only. The winner would have to deliver within 5 days

Sample reference : velmorq.com/html/brightneighbour/#
(previous winner cant deliver)
*All of our wording and graphic content are updated, designer wouldn't involve in recreating any content.
Designer may use template or own material. delivery in html and implement on our WordPress server

please submit about us the project submission.
upon the winning, you have to maintain sub content / pages and submit the full site with your improved version of full websites including inner pages

Low design quality

Target Market(s)

general audience

Industry/Entity Type

social service

Number of Pages Required

5+ page

Requirements
Must have
• feeling and look similar to pobrix dot com
Nice to have
• extend the same style to other pages

```html
<!DOCTYPE html>
<html lang="en">
<head>
<meta charset="utf-8">
<title>Bright Neighbour — New way of Giving</title>
<link rel="stylesheet" href="https://fonts.googleapis.com/css2?family=Poppins:wght@300;400;500;600;700&display=swap">
<style>
:root{
  --coral:#f5636b;
  --coral-soft:#fbd3d5;
  --coral-pale:#fff1f1;
  --ink:#1f1f26;
  --muted:#77777f;
  --line:#e6e6ec;
  --lavender:#eef0f8;
  --white:#ffffff;
}
*{box-sizing:border-box;margin:0;padding:0}
html,body{width:1200px;height:4451px;overflow:hidden;background:var(--white)}
body{font-family:"Poppins",sans-serif;color:var(--ink);position:relative}
.abs{position:absolute}
.label{color:var(--coral);font-size:13px;font-weight:500}
.h1{font-size:46px;font-weight:600;line-height:54px;letter-spacing:.5px}
.text{font-size:13.5px;line-height:26px;color:var(--muted);font-weight:300}
.btn{position:absolute;background:var(--coral);color:var(--white);border-radius:24px;font-size:13px;font-weight:500;display:flex;align-items:center;justify-content:center;box-shadow:0 6px 14px rgba(245,99,107,.28)}
.brand{position:absolute;display:flex;align-items:center;gap:8px;color:var(--coral);font-weight:600;white-space:nowrap}
.brand .dot{border-radius:50%;background:var(--coral);flex:none}
.nav a{position:absolute;top:37px;font-size:13px;font-weight:500;color:var(--ink);text-decoration:none}
.nav a.active{color:var(--coral)}
.media{position:absolute;overflow:hidden}
.wave{position:absolute;left:0;width:1200px}
.partners{position:absolute;left:0;top:1314px;width:1200px;height:494px}
.cell{position:absolute;width:181px;height:99px;border:1px solid var(--line);display:flex;align-items:center;justify-content:center;background:var(--white)}
.badge{width:104px;height:34px;border-radius:6px;background:#e9e9ef}
.card{position:absolute;top:1798px;width:248px;height:308px;background:var(--white);box-shadow:0 2px 10px rgba(30,30,60,.08);text-align:center}
.card .icon{width:90px;height:90px;border-radius:50%;background:var(--coral-pale);margin:28px auto 0;display:flex;align-items:center;justify-content:center}
.card h3{font-size:14.5px;font-weight:600;margin-top:24px}
.card p{font-size:13px;line-height:26px;color:var(--muted);font-weight:300;margin:8px 14px 0}
.card .more{display:block;margin-top:16px;color:var(--coral);font-size:12px;font-weight:600}
.why-item{position:absolute;left:629px;width:520px;height:90px}
.why-item .circle{position:absolute;left:0;top:0;width:90px;height:90px;border-radius:50%;background:var(--coral);box-shadow:0 0 0 8px var(--coral-soft);display:flex;align-items:center;justify-content:center}
.why-item h4{position:absolute;left:109px;top:4px;font-size:14.5px;font-weight:600}
.why-item p{position:absolute;left:109px;top:30px;width:380px;font-size:13px;line-height:26px;color:var(--muted);font-weight:300}
.member{position:absolute;top:2993px;width:248px;height:366px;background:var(--white);box-shadow:0 2px 10px rgba(30,30,60,.07);text-align:center}
.member .photo{height:245px}
.member h5{font-size:14px;font-weight:600;margin-top:17px}
.member span{display:block;font-size:13px;color:var(--muted);line-height:26px;font-weight:300}
.member.featured{background:var(--coral)}
.member.featured h5,.member.featured span{color:var(--white)}
.gift-item{position:absolute;left:60px;width:500px;height:90px}
.gift-item .circle{position:absolute;left:0;top:0;width:90px;height:90px;border-radius:50%;background:var(--coral);display:flex;align-items:center;justify-content:center}
.gift-item h4{position:absolute;left:108px;top:8px;font-size:18px;font-weight:600}
.gift-item p{position:absolute;left:108px;top:36px;width:380px;font-size:13px;line-height:26px;color:var(--ink);font-weight:300}
.gift-item b{color:var(--coral);font-weight:500}
.footer h6{position:absolute;font-size:13px;font-weight:600}
.footer .links a{position:absolute;font-size:12.5px;color:var(--muted);text-decoration:none;font-weight:300}
.social{position:absolute;top:4322px;width:26px;height:26px;border-radius:50%;background:var(--coral)}
.input{position:absolute;left:894px;top:4241px;width:245px;height:36px;border-radius:18px;background:var(--white);font-size:12px;color:var(--muted);padding-left:16px;display:flex;align-items:center;font-weight:300}
</style>
</head>
<body>

<!-- header -->
<div class="brand" style="left:60px;top:36px;font-size:15px"><span class="dot" style="width:14px;height:14px"></span>Bright Neighbour</div>
<nav class="nav">
  <a class="active" style="left:565px">Home</a>
  <a style="left:635px">About Us</a>
  <a style="left:728px">Our Story</a>
  <a style="left:821px">Social Impact</a>
  <a style="left:946px">Join Us</a>
</nav>
<div class="btn" style="left:1027px;top:26px;width:112px;height:43px">Sign Up</div>

<!-- hero -->
<div class="abs" role="img" aria-label="Soft striped accent circle" style="left:14px;top:120px;width:124px;height:128px;border-radius:50%;background:linear-gradient(135deg,#fdeeee,#fff7f7)"></div>
<h1 class="abs" style="left:60px;top:274px;font-size:46px;font-weight:600;line-height:54px">New way of Giving<br><span style="color:var(--coral)">Social Inclusion</span></h1>
<p class="abs text" style="left:60px;top:393px;width:380px">We believe in authentic social responsibility is driven from individuals and businesses.</p>
<div class="btn" style="left:60px;top:463px;width:156px;height:44px">Sign Up Now</div>
<div class="media" role="img" aria-label="Illustration of the Bright Neighbour mobile app screens over a coral blob" style="left:519px;top:150px;width:636px;height:470px;border-radius:46% 54% 42% 58% / 50% 44% 56% 50%;background:radial-gradient(circle at 60% 50%,#f8777e,#f5636b 60%,#fbd3d5)"></div>

<!-- about -->
<svg class="wave" style="top:640px;height:570px" viewBox="0 0 1200 570" preserveAspectRatio="none" aria-hidden="true">
  <defs><linearGradient id="aboutBg" x1="0" y1="0" x2="0" y2="1"><stop offset="0" stop-color="#ffffff"/><stop offset="1" stop-color="#eceef8"/></linearGradient></defs>
  <path d="M0 0H1200V560C1050 490 900 520 720 555C520 590 300 500 0 525Z" fill="url(#aboutBg)"/>
</svg>
<div class="media" role="img" aria-label="Animated video still of a colourful city illustration with a play button" style="left:60px;top:754px;width:473px;height:306px;background:linear-gradient(180deg,#cfd8e6 0%,#e7d7dc 45%,#e8a4a6 100%)">
  <svg class="abs" style="left:207px;top:124px" width="60" height="60" viewBox="0 0 60 60"><circle cx="30" cy="30" r="30" fill="#1f1f26"/><path d="M24 19L41 30 24 41Z" fill="#fff"/></svg>
</div>
<div class="abs label" style="left:635px;top:764px">About Us</div>
<h2 class="abs" style="left:635px;top:784px;font-size:36px;font-weight:600;line-height:50px">Hello, Bright Neighbours!</h2>
<p class="abs text" style="left:635px;top:855px;width:478px">Just like you, we resonate with a variety of social causes. At the core of everything, we believe that many societal challenges could be minimized merely by being more kind to one another and showing more trust in each other, especially during these difficult times.</p>
<div class="btn" style="left:635px;top:989px;width:140px;height:42px">Read More</div>

<!-- partners -->
<div class="abs label" style="left:0;width:1200px;text-align:center;top:1266px">Our Partners</div>
<div class="partners" role="list" aria-label="Partner organisations">
  <div class="cell" role="listitem" style="left:147px;top:0"><div class="badge"></div></div>
  <div class="cell" role="listitem" style="left:328px;top:0"><div class="badge"></div></div>
  <div class="cell" role="listitem" style="left:509px;top:0"><div class="badge"></div></div>
  <div class="cell" role="listitem" style="left:690px;top:0"><div class="badge"></div></div>
  <div class="cell" role="listitem" style="left:871px;top:0"><div class="badge"></div></div>
  <div class="cell" role="listitem" style="left:147px;top:98px"><div class="badge"></div></div>
  <div class="cell" style="left:328px;top:98px"></div>
  <div class="cell" role="listitem" style="left:509px;top:98px"><div class="badge"></div></div>
  <div class="cell" style="left:690px;top:98px"></div>
  <div class="cell" role="listitem" style="left:871px;top:98px"><div class="badge"></div></div>
  <div class="cell" role="listitem" style="left:328px;top:196px"><div class="badge"></div></div>
  <div class="cell" style="left:509px;top:196px"></div>
  <div class="cell" role="listitem" style="left:690px;top:196px"><div class="badge"></div></div>
  <div class="cell" role="listitem" style="left:509px;top:294px"><div class="badge"></div></div>
</div>

<!-- services -->
<div class="card" style="left:59px">
  <div class="icon"><svg width="44" height="44" viewBox="0 0 44 44" fill="none" stroke="#f5636b" stroke-width="1.6"><circle cx="12" cy="12" r="4"/><circle cx="22" cy="10" r="4"/><circle cx="32" cy="12" r="4"/><path d="M6 34V22a6 6 0 0 1 12 0M16 34V20a6 6 0 0 1 12 0v14M26 22a6 6 0 0 1 12 0v12"/></svg></div>
  <h3>Bright Neighbours</h3>
  <p>You might be a busy professional with a strong desire to help our community practically.</p>
  <span class="more">READ MORE</span>
</div>
<div class="card" style="left:335px">
  <div class="icon"><svg width="44" height="44" viewBox="0 0 44 44" fill="none" stroke="#f5636b" stroke-width="1.6"><path d="M8 38h28M12 38V18h10v20M22 38V8h10v30M15 22h4M15 27h4M15 32h4M25 13h4M25 18h4M25 23h4M25 28h4"/></svg></div>
  <h3>Bright Business</h3>
  <p>Traditionally, Corporate Social Responsibility (CSR) has been for the "big guys" who run...</p>
  <span class="more">READ MORE</span>
</div>
<div class="card" style="left:614px">
  <div class="icon"><svg width="44" height="44" viewBox="0 0 44 44" fill="none" stroke="#f5636b" stroke-width="1.6"><path d="M6 16l4-9h24l4 9M6 16h32v4a4 4 0 0 1-8 0 4 4 0 0 1-8 0 4 4 0 0 1-8 0 4 4 0 0 1-8 0zM9 24v14h26V24M18 38V29h8v9"/></svg></div>
  <h3>Merchant</h3>
  <p>In Bright Neighbour, we make it convenient and easy to blend social impact to your shop...</p>
  <span class="more">READ MORE</span>
</div>
<div class="card" style="left:890px">
  <div class="icon"><svg width="44" height="44" viewBox="0 0 44 44" fill="none" stroke="#f5636b" stroke-width="1.6"><rect x="7" y="16" width="30" height="8"/><rect x="9" y="24" width="26" height="14"/><path d="M22 16v22M22 16c-4-8-12-6-9-1M22 16c4-8 12-6 9-1"/></svg></div>
  <h3>The Bright Gift</h3>
  <p>Unique Gift, Real Impact - A gift that meaningfully connects people to do good together.</p>
  <span class="more">READ MORE</span>
</div>

<!-- why us -->
<h2 class="abs" style="left:0;width:1200px;text-align:center;top:2186px;font-size:44px;font-weight:600">Why Us?</h2>
<div class="media" role="img" aria-label="Bold abstract illustration of people sharing and giving" style="left:60px;top:2301px;width:509px;height:357px;box-shadow:0 4px 12px rgba(0,0,0,.12);background:linear-gradient(135deg,#e9e4da 0%,#f4b8c6 35%,#f5b43a 55%,#243aa8 80%,#1f1f26 100%)"></div>
<div class="why-item" style="top:2291px">
  <div class="circle"><svg width="44" height="44" viewBox="0 0 44 44" fill="none" stroke="#fff" stroke-width="1.6"><circle cx="24" cy="16" r="8"/><path d="M24 12v8M21 14h5M21 18h5M4 34l8-6h10l10-4M4 26l8-4h8"/></svg></div>
  <h4>Affordable</h4>
  <p>Doing good does not need to be only on a large scale. We make it practical and resourceful.</p>
</div>
<div class="why-item" style="top:2433px">
  <div class="circle"><svg width="44" height="44" viewBox="0 0 44 44" fill="none" stroke="#fff" stroke-width="1.8"><circle cx="19" cy="19" r="11"/><path d="M27 27l10 10"/></svg></div>
  <h4>Transparent</h4>
  <p>Monitor your account to see where each contribution of yours goes.</p>
</div>
<div class="why-item" style="top:2576px">
  <div class="circle"><svg width="44" height="44" viewBox="0 0 44 44" fill="none" stroke="#fff" stroke-width="1.6"><path d="M6 6v32h32M10 30l8-9 6 5 10-13"/></svg></div>
  <h4>Measurable</h4>
  <p>Access your account any time to view the full contributions report.</p>
</div>

<!-- social impact -->
<svg class="wave" style="top:2732px;height:700px" viewBox="0 0 1200 700" preserveAspectRatio="none" aria-hidden="true">
  <defs><linearGradient id="impactBg" x1="0" y1="0" x2="0" y2="1"><stop offset="0" stop-color="#eceef8"/><stop offset=".55" stop-color="#f7f8fc"/><stop offset="1" stop-color="#ffffff"/></linearGradient></defs>
  <path d="M0 30C200 -10 420 60 640 50C880 40 1050 0 1200 20V700H0Z" fill="url(#impactBg)"/>
</svg>
<div class="abs label" style="left:0;width:1200px;text-align:center;top:2830px">Social Impact</div>
<h2 class="abs h1" style="left:0;width:1200px;text-align:center;top:2857px">Our Social Impact<br>Ambassadors and Mentors</h2>
<div class="member" style="left:59px"><div class="photo" role="img" aria-label="Portrait photo of an ambassador" style="background:linear-gradient(180deg,#3a3e44,#5c6066)"></div><h5>Name</h5><span>Company</span><span>Designation</span></div>
<div class="member featured" style="left:335px"><div class="photo" role="img" aria-label="Portrait photo of an ambassador" style="background:linear-gradient(180deg,#efe3d4,#c9a487)"></div><h5>Name</h5><span>Company</span><span>Designation</span></div>
<div class="member" style="left:614px"><div class="photo" role="img" aria-label="Portrait photo of a mentor" style="background:linear-gradient(180deg,#5d646b,#8b9096)"></div><h5>Name</h5><span>Company</span><span>Designation</span></div>
<div class="member" style="left:890px"><div class="photo" role="img" aria-label="Portrait photo of a mentor" style="background:linear-gradient(180deg,#f2f1ef,#d9cfc7)"></div><h5>Name</h5><span>Company</span><span>Designation</span></div>

<!-- gift -->
<div class="abs label" style="left:73px;top:3504px">Simple . Fun . Impactful.</div>
<h2 class="abs h1" style="left:73px;top:3528px">Inspire others with<br>a meaningful gift.</h2>
<p class="abs" style="left:73px;top:3656px;width:480px;font-size:13px;line-height:26px;font-weight:300">Unique Gift, Real Impact - A gift that meaningfully connects people to do good together.</p>
<div class="gift-item" style="top:3736px">
  <div class="circle"><svg width="44" height="44" viewBox="0 0 44 44" fill="none" stroke="#fff" stroke-width="1.6"><rect x="7" y="16" width="30" height="8"/><rect x="9" y="24" width="26" height="14"/><path d="M22 16v22M22 16c-4-8-12-6-9-1M22 16c4-8 12-6 9-1"/></svg></div>
  <h4>Gift &amp; Giving</h4>
  <p>Be it a corporate gift, a giveaway for a unique occasion, or an entirely new approach... <b>READ MORE</b></p>
</div>
<div class="gift-item" style="top:3864px">
  <div class="circle"><svg width="44" height="44" viewBox="0 0 44 44" fill="none" stroke="#fff" stroke-width="1.6"><path d="M8 20h7v18H8zM15 21l6-12c3 0 4 2 3 6l-1 5h10c3 0 4 2 3 4l-3 11c-1 2-2 3-4 3H15"/></svg></div>
  <h4>Inspire Kindness</h4>
  <p>Create a brand-new experience and inspire someone to participate in the ripple effect of... <b>READ MORE</b></p>
</div>
<div class="media" role="img" aria-label="Photo of a pay-it-forward gift card tied with a coral ribbon, with small gift and lightbulb icons" style="left:616px;top:3545px;width:510px;height:376px;background:linear-gradient(135deg,#f7b4b8 0%,#f3f0ee 45%,#e4e0df 100%)"></div>
<div class="abs" aria-hidden="true" style="left:640px;top:3493px;width:120px;height:120px;border-radius:50%;background:var(--white);box-shadow:0 4px 14px rgba(0,0,0,.1)"></div>
<div class="abs" aria-hidden="true" style="left:972px;top:3856px;width:118px;height:118px;border-radius:50%;background:var(--white);box-shadow:0 4px 14px rgba(0,0,0,.1)"></div>
<div class="brand" style="left:704px;top:3894px;font-size:13px"><span class="dot" style="width:12px;height:12px"></span>Bright Neighbour</div>

<!-- footer -->
<svg class="wave" style="top:4060px;height:391px" viewBox="0 0 1200 391" preserveAspectRatio="none" aria-hidden="true">
  <path d="M0 20C250 60 500 0 760 20C950 34 1100 30 1200 10V391H0Z" fill="#fdf0f0"/>
</svg>
<footer class="footer">
  <div class="brand" style="left:60px;top:4160px;font-size:16px"><span class="dot" style="width:16px;height:16px"></span>Bright Neighbour</div>
  <h6 style="left:60px;top:4219px">Follow us and stay updated!</h6>
  <p class="abs" style="left:60px;top:4244px;width:240px;font-size:11.5px;line-height:21px;color:var(--muted);font-weight:300">A Harbourline Social Enterprise.<br>In a world where you can be anything, be kind.</p>
  <span class="social" style="left:61px"></span>
  <span class="social" style="left:99px"></span>
  <span class="social" style="left:137px"></span>
  <span class="social" style="left:174px"></span>

  <h6 style="left:339px;top:4146px">Useful Links</h6>
  <div class="links">
    <a style="left:339px;top:4187px">Home</a>
    <a style="left:339px;top:4217px">About Us</a>
    <a style="left:339px;top:4246px">Our Story</a>
    <a style="left:339px;top:4277px">Social Impact</a>
    <a style="left:339px;top:4307px">Bright Neighbour</a>
    <a style="left:616px;top:4187px">Bright Business</a>
    <a style="left:616px;top:4217px">Merchant</a>
    <a style="left:616px;top:4246px">The Bright Gift</a>
    <a style="left:616px;top:4277px">FAQs</a>
    <a style="left:616px;top:4307px">Contact Us</a>
  </div>

  <h6 style="left:894px;top:4146px">Subscribe to Our Newsletter</h6>
  <p class="abs" style="left:894px;top:4173px;width:250px;font-size:11.5px;line-height:21px;color:var(--muted);font-weight:300">Let's stay in touch! We would like to keep you inspired with our Kindness stories and community events.</p>
  <div class="input">Enter email here...</div>
  <div class="abs" style="left:894px;top:4291px;width:10px;height:10px;border:1px solid #ccc;background:var(--white)"></div>
  <p class="abs" style="left:910px;top:4286px;width:232px;font-size:11.5px;line-height:21px;color:var(--muted);font-weight:300">By continuing, you accept the privacy policy</p>
  <div class="btn" style="left:892px;top:4336px;width:247px;height:44px;border-radius:22px">Subscribe Now</div>

  <p class="abs" style="left:0;width:1200px;text-align:center;top:4421px;font-size:11px;color:var(--muted)">© <span style="color:var(--coral)">BRIGHT NEIGHBOUR HQ</span> - 2021. All Rights Reserved.</p>
</footer>

</body>
</html>
```